Travel Agency Website - Simple General

Need a 7 page simple design that is pretty repetitive. Need to be able to load quickly that is SEO optimized. Trying to give ideas on what they can do, be personal as we are local, but at the same time come across as professional and get information easily with little burden.

- Landing Page
- Brimwell Vacations Page
- Family Trips
- Road Trips from Texas
- Other Destinations
- About Us Page
- Contact Us Page

Target Market(s)

Families

Coding

Coded - Design and coding required

Number of Pages Required

5+ page

Colors

Designer to choose colors to be used in the design.

Requirements
Must have
• Like it to flow easily with our logo. Use that for colors, etc.

```html
<!DOCTYPE html>
<html lang="en">
<head>
<meta charset="utf-8">
<title>Meander Travel Co. – Website Pages</title>
<link href="https://fonts.googleapis.com/css2?family=Poppins:wght@400;500;600;700&display=swap" rel="stylesheet">
<style>
:root{
  --teal:#0b4a5a;
  --teal-dark:#083d4a;
  --gold:#b9842f;
  --gold-light:#d2a04c;
  --paper:#ebe8e2;
  --ink:#1d3b44;
  --muted:#7a8488;
  --line:#e0e4e6;
  --card:#f6f6f5;
  --white:#ffffff;
}
*{box-sizing:border-box;margin:0;padding:0}
html,body{width:1200px;height:2187px;overflow:hidden;background:var(--white)}
body{font-family:'Poppins',sans-serif;color:var(--ink);position:relative}
.board{position:absolute;top:0;left:0;width:1414px;height:2577px;transform:scale(.8487);transform-origin:0 0}

.page{position:absolute;width:474px;background:var(--white);box-shadow:0 6px 28px rgba(0,0,0,.09);overflow:hidden}

/* header */
.topbar{height:26px;background:var(--paper);position:relative;display:flex;align-items:center;justify-content:space-between;padding:0 76px}
.topbar .phone{display:flex;align-items:center;gap:3px;font-size:5.5px;font-weight:700;color:var(--teal)}
.topbar .phone svg{width:5px;height:5px}
.topbar .brand{position:absolute;left:50%;top:4px;transform:translateX(-50%);font-size:7.5px;font-weight:600;color:var(--teal);background:var(--paper);padding:3px 4px;border-radius:3px;z-index:2}
.social{display:flex;gap:8px}
.social span{width:5px;height:5px;border-radius:50%;background:var(--gold);display:block}
.nav{height:20px;background:var(--gold);border-top:1.5px solid var(--gold-light);border-bottom:1.5px solid var(--gold-light);display:flex;justify-content:center;align-items:center;gap:13px;font-size:3.6px;color:var(--white);letter-spacing:.1px;text-transform:uppercase;box-shadow:inset 0 2px 0 rgba(255,255,255,.25),inset 0 -2px 0 rgba(255,255,255,.25)}

/* hero */
.hero{position:relative;height:134px;display:flex;flex-direction:column;align-items:center;justify-content:center;text-align:center;color:var(--white);padding-bottom:22px}
.hero-beach{background:linear-gradient(180deg,#a99c8c 0%,#cdb591 30%,#e0c596 40%,#6f9290 47%,#2f6b72 60%,#3e7476 72%,#a39582 88%,#c4b59f 100%)}
.hero-canyon{background:linear-gradient(180deg,#6e3a2a 0%,#a4533a 30%,#8b4430 55%,#5b4a44 75%,#3f3b3a 100%)}
.hero h1{font-size:12.5px;font-weight:600;text-shadow:0 1px 3px rgba(0,0,0,.3)}
.hero p{font-size:3.4px;margin-top:4px;opacity:.95}
.tear{position:absolute;left:0;bottom:-1px;width:100%;height:16px}

/* thumbnails */
.thumbs{display:flex;gap:3px;justify-content:center;margin-top:42px}
.thumb{width:59px;height:59px;border-radius:3px}
.t-road{background:linear-gradient(180deg,#c9865f,#7d4a35 55%,#3b3634)}
.t-peak{background:linear-gradient(180deg,#7fa9cf,#c7d8e6 45%,#6b6f6d)}
.t-shore{background:linear-gradient(180deg,#e7d1b8,#f2dcc0 45%,#a9c4c8 70%,#d8c7ae)}
.t-street{background:linear-gradient(180deg,#c9b7a3,#b05664 55%,#6a4c44)}
.t-selfie{background:linear-gradient(180deg,#9cc7e6,#e0b055 55%,#5a6b7a)}
.t-reef{background:linear-gradient(180deg,#2b8fa3,#1d6f86 55%,#d49a4f)}
.t-hotel{background:linear-gradient(180deg,#c7bfb5,#f0ece6 55%,#5b4d44)}
.t-map{background:linear-gradient(180deg,#efe8df,#d9c2a5 55%,#76594a)}
.t-group{background:linear-gradient(180deg,#d6d0c4,#c69a63 55%,#5c4d45)}

/* form card */
.card{width:330px;margin:21px auto 0;background:var(--card);border-radius:6px;padding:12px 7px 8px}
.card + .card{margin-top:11px}
.card-title{height:24px;margin:0 1px;background:var(--teal);color:var(--white);border-radius:6px;display:flex;align-items:center;justify-content:center;font-size:6.8px;font-weight:600}
.field{height:19px;margin:6px 4px 0;background:var(--white);border:1px solid var(--line);border-radius:3px;display:flex;align-items:center;justify-content:space-between;padding:0 7px;font-size:3.3px;color:#5e676b}
.field.area{height:65px;align-items:flex-start;padding-top:8px}
.label{margin:4px 4px 0;font-size:3.2px;font-weight:700;color:var(--teal)}
.label + .field{margin-top:2px}
.chev{width:4px;height:3px}
.cal{width:3.5px;height:3.5px;border:.8px solid #555;border-radius:.5px}
.btn{height:24px;margin:6px 0 0;background:var(--gold);border-radius:6px;color:var(--white);display:flex;align-items:center;justify-content:center;font-size:6.4px;font-weight:600}

/* footer */
.footer{position:absolute;left:0;right:0;bottom:0;height:70px;background:var(--teal);color:var(--white)}
.footer .ftear{position:absolute;left:0;top:-14px;width:100%;height:15px}
.footer .fbrand{position:absolute;left:62px;top:22px;font-size:11px;font-weight:600}
.finfo{position:absolute;left:175px;top:18px;display:flex;gap:14px;font-size:3.4px;align-items:center}
.finfo span{display:flex;align-items:center;gap:2px}
.finfo svg{width:3.6px;height:3.6px}
.fcopy{position:absolute;left:175px;top:38px;font-size:3.3px}
.flinks{position:absolute;right:52px;top:38px;font-size:3.3px;display:flex;gap:3px}
.fsocial{position:absolute;right:56px;top:17px;display:flex;gap:3px}
.fsocial span{width:6px;height:6px;border-radius:50%;background:var(--gold);display:block}

/* landing */
.panels{position:relative;height:290px;background:var(--teal)}
.panel{position:absolute;top:0;height:290px;text-align:center;color:var(--white);padding-top:24px}
.panel h2{font-size:5.6px;font-weight:600;line-height:1.15}
.panel p{font-size:2.9px;margin-top:3px;opacity:.95}
.go{width:17px;height:17px;border-radius:50%;background:var(--white);margin:6px auto 0;display:flex;align-items:center;justify-content:center}
.go svg{width:7px;height:7px}
.p-castle{left:0;width:140px;background:linear-gradient(180deg,#2e4e7a 0%,#5b5e8a 25%,#c58a5c 50%,#3b3a4a 75%,#2b2a30 100%);clip-path:polygon(0 0,100% 0,97% 22%,99% 45%,95% 70%,97% 88%,90% 92%,70% 90%,45% 93%,20% 90%,0 93%)}
.p-family{left:130px;width:125px;background:linear-gradient(180deg,#3b6f9e 0%,#7fa6c6 30%,#e9ecec 55%,#c9c6bc 80%,#6f7a5b 100%);clip-path:polygon(6% 0,100% 0,97% 30%,100% 55%,96% 80%,98% 95%,75% 93%,45% 96%,15% 92%,4% 94%,8% 70%,3% 40%)}
.p-texas{left:245px;width:125px;background:linear-gradient(180deg,#3d7ab3 0%,#8db6d8 30%,#d6d4cc 55%,#7c7a74 80%,#4e4d4c 100%);clip-path:polygon(7% 0,100% 0,95% 25%,99% 50%,94% 75%,97% 92%,70% 90%,40% 94%,10% 91%,5% 65%,9% 40%)}
.p-other{left:360px;width:114px;background:linear-gradient(180deg,#8fb8d8 0%,#c5d9e6 30%,#e4d7c4 55%,#b98b6b 80%,#8a8883 100%);clip-path:polygon(8% 0,100% 0,100% 92%,70% 95%,40% 91%,12% 94%,6% 70%,10% 45%,5% 20%)}
.page.landing .footer{height:68px}

/* road table */
.section-head{text-align:center;margin-top:34px}
.section-head h2{font-size:11px;font-weight:600;color:var(--teal)}
.section-head p{font-size:3.3px;color:#555;margin-top:3px}
.trips{width:312px;margin:9px auto 0;border-collapse:separate;border-spacing:0;font-size:3.3px;border:1px solid var(--line);border-radius:6px;overflow:hidden}
.trips th{background:var(--teal);color:var(--white);font-weight:600;height:22px;text-align:left;padding-left:10px;font-size:3.5px}
.trips td{height:17px;padding-left:10px;color:#4f5a5e;border-right:1px solid var(--line)}
.trips td:last-child{border-right:0}
.trips tr.alt td{background:#e7eef0}

/* about */
.about{display:flex;gap:20px;margin:33px 0 0 78px}
.about-photo{width:140px;height:140px;border-radius:50%;background:linear-gradient(180deg,#c7d0cf 0%,#e6dccb 40%,#a07f62 70%,#5a5450 100%);flex-shrink:0}
.about-text{width:160px;padding-top:4px}
.about-text h2{font-size:11px;font-weight:600;color:var(--teal)}
.about-text p{font-size:3.3px;line-height:1.45;color:#4a5458;margin-top:5px}

/* contact */
.chips{display:flex;gap:6px;margin:33px 0 0 72px}
.chip{height:26px;background:var(--card);border-radius:6px;display:flex;align-items:center;gap:6px;padding:0 8px}
.chip .dot{width:13px;height:13px;border-radius:50%;background:var(--gold);display:flex;align-items:center;justify-content:center}
.chip .dot svg{width:6px;height:6px}
.chip b{display:block;font-size:6px;font-weight:600;color:var(--teal);line-height:1}
.chip small{font-size:4.4px;color:var(--ink)}
.page.contact .card{margin-top:5px}

/* brand mark */
.mark{position:absolute;left:300px;top:2085px;width:330px;height:290px;display:flex;align-items:center;justify-content:center;text-align:center;font-size:50px;font-weight:600;line-height:1.05;color:var(--teal)}
</style>
</head>
<body>
<div class="board">

<!-- Landing -->
<section class="page landing" style="left:223px;top:156px;height:380px">
  <header class="topbar">
    <div class="phone"><svg viewBox="0 0 10 10"><path d="M2 1l2 0 1 2.5-1.3 1a6 6 0 0 0 2.8 2.8l1-1.3L10 7v2a1 1 0 0 1-1 1A9 9 0 0 1 0 1a1 1 0 0 1 1-1z" fill="#b9842f"/></svg>111.111.1111</div>
    <div class="brand">Meander</div>
    <div class="social"><span></span><span></span></div>
  </header>
  <nav class="nav"><span>Home</span><span>Brimwell Vacations</span><span>Family Trips</span><span>Texas Road Trips</span><span>Other Destinations</span><span>About Us</span><span>Contact</span></nav>
  <div class="panels">
    <div class="panel p-castle" role="img" aria-label="Photo of a lit castle at dusk with families watching"><h2>Brimwell Vacations<br>Land and Sea</h2><p>Magical Brimwell trips planned for families</p><div class="go"><svg viewBox="0 0 10 10"><path d="M2 5h6M5.5 2.5 8 5 5.5 7.5" fill="none" stroke="#0b4a5a" stroke-width="1.2"/></svg></div></div>
    <div class="panel p-family" role="img" aria-label="Photo of grandparents holding a child outdoors"><h2>Family<br>Trips</h2><p>Relaxing vacations for all ages</p><div class="go"><svg viewBox="0 0 10 10"><path d="M2 5h6M5.5 2.5 8 5 5.5 7.5" fill="none" stroke="#0b4a5a" stroke-width="1.2"/></svg></div></div>
    <div class="panel p-texas" role="img" aria-label="Photo of a state capitol building down a city street"><h2>Texas Road Trips<br>(Piney Road Van Rentals)</h2><p>Explore Texas with flexible van adventures</p><div class="go"><svg viewBox="0 0 10 10"><path d="M2 5h6M5.5 2.5 8 5 5.5 7.5" fill="none" stroke="#0b4a5a" stroke-width="1.2"/></svg></div></div>
    <div class="panel p-other" role="img" aria-label="Photo of a couple relaxing near a ferris wheel"><h2>Other<br>Destinations</h2><p>Explore exciting destinations worldwide</p><div class="go"><svg viewBox="0 0 10 10"><path d="M2 5h6M5.5 2.5 8 5 5.5 7.5" fill="none" stroke="#0b4a5a" stroke-width="1.2"/></svg></div></div>
  </div>
  <footer class="footer">
    <div class="fbrand">Meander</div>
    <div class="finfo"><span><svg viewBox="0 0 10 10"><path d="M2 1l2 0 1 2.5-1.3 1a6 6 0 0 0 2.8 2.8l1-1.3L10 7v2a1 1 0 0 1-1 1A9 9 0 0 1 0 1a1 1 0 0 1 1-1z" fill="#fff"/></svg>111.111.1111</span><span><svg viewBox="0 0 10 10"><rect x="0" y="2" width="10" height="7" fill="#fff"/></svg>hello@meandertravel.example</span></div>
    <div class="fcopy">2026 Meander Travel Co. All Right Reserved</div>
    <div class="fsocial"><span></span><span></span></div>
    <div class="flinks"><span>Terms &amp;</span><span>|</span><span>Conditions</span><span>|</span><span>Privacy Policy</span></div>
  </footer>
</section>

<!-- Brimwell Vacations -->
<section class="page" style="left:716px;top:156px;height:1066px">
  <header class="topbar">
    <div class="phone"><svg viewBox="0 0 10 10"><path d="M2 1l2 0 1 2.5-1.3 1a6 6 0 0 0 2.8 2.8l1-1.3L10 7v2a1 1 0 0 1-1 1A9 9 0 0 1 0 1a1 1 0 0 1 1-1z" fill="#b9842f"/></svg>111.111.1111</div>
    <div class="brand">Meander</div>
    <div class="social"><span></span><span></span></div>
  </header>
  <nav class="nav"><span>Home</span><span>Brimwell Vacations</span><span>Family Trips</span><span>Texas Road Trips</span><span>Other Destinations</span><span>About Us</span><span>Contact</span></nav>
  <div class="hero hero-beach" role="img" aria-label="Photo of a beach at sunset">
    <h1>Plan Your Brimwell Vacation</h1>
    <p>Choose the option that fits your dream trip and fill out the form below. We'll take care of the rest.</p>
    <svg class="tear" viewBox="0 0 474 16" preserveAspectRatio="none"><path d="M0 16V9l18 2 14-5 20 4 22-6 16 5 24-3 18 4 20-6 26 5 18-2 22 4 20-5 24 3 18-4 22 5 20-3 26 4 18-6 22 5 20-2 24 3 22-5 20 4V16z" fill="#fff"/></svg>
  </div>
  <div class="thumbs">
    <div class="thumb t-hotel" role="img" aria-label="Photo of a hotel room"></div>
    <div class="thumb t-map" role="img" aria-label="Photo of travelers reading a map"></div>
    <div class="thumb t-group" role="img" aria-label="Photo of friends on a trip"></div>
    <div class="thumb t-street" role="img" aria-label="Photo of travelers with suitcases"></div>
    <div class="thumb t-selfie" role="img" aria-label="Photo of travelers taking a selfie"></div>
    <div class="thumb t-reef" role="img" aria-label="Photo of an underwater reef"></div>
  </div>
  <form class="card">
    <div class="card-title">Brimwell World / Brimwell Land</div>
    <div class="field">How Many People? (1-20)</div>
    <div class="label">Start Date</div>
    <div class="field">mm/dd/yyyy<span class="cal"></span></div>
    <div class="label">End Date</div>
    <div class="field">mm/dd/yyyy<span class="cal"></span></div>
    <div class="field">How Many Days at the Parks? (1-10)<span>⇕</span></div>
    <div class="field">Any Preferred Resorts?</div>
    <div class="field">Preferred Resort 1<svg class="chev" viewBox="0 0 10 6"><path d="M1 1l4 4 4-4" fill="none" stroke="#777" stroke-width="1.5"/></svg></div>
    <div class="field">Preferred Resort 2<svg class="chev" viewBox="0 0 10 6"><path d="M1 1l4 4 4-4" fill="none" stroke="#777" stroke-width="1.5"/></svg></div>
    <div class="field">Trip Type<svg class="chev" viewBox="0 0 10 6"><path d="M1 1l4 4 4-4" fill="none" stroke="#777" stroke-width="1.5"/></svg></div>
    <div class="field area">Any additional notes</div>
    <div class="btn">Submit Brimwell Trip</div>
  </form>
  <form class="card">
    <div class="card-title">Brimwell Cruise</div>
    <div class="field">How Many People? (1-20)</div>
    <div class="field">Months you would like to travel</div>
    <div class="field">How many cruise nights?</div>
    <div class="field">Any specific cruise ship?</div>
    <div class="field">Trip Type<svg class="chev" viewBox="0 0 10 6"><path d="M1 1l4 4 4-4" fill="none" stroke="#777" stroke-width="1.5"/></svg></div>
    <div class="field area">Any additional notes</div>
    <div class="btn">Submit Brimwell Trip</div>
  </form>
  <footer class="footer" style="height:68px">
    <svg class="ftear" viewBox="0 0 474 15" preserveAspectRatio="none"><path d="M0 15V8l22-3 18 4 24-5 20 3 22-4 18 5 26-2 20 3 22-6 18 4 24-2 20 4 22-5 18 3 26-4 20 5 22-3 18 2 24-6 22 1 18-4 16 3 20-3V15z" fill="#0b4a5a"/></svg>
    <div class="fbrand">Meander</div>
    <div class="finfo"><span><svg viewBox="0 0 10 10"><path d="M2 1l2 0 1 2.5-1.3 1a6 6 0 0 0 2.8 2.8l1-1.3L10 7v2a1 1 0 0 1-1 1A9 9 0 0 1 0 1a1 1 0 0 1 1-1z" fill="#fff"/></svg>111.111.1111</span><span><svg viewBox="0 0 10 10"><rect x="0" y="2" width="10" height="7" fill="#fff"/></svg>hello@meandertravel.example</span></div>
    <div class="fcopy">2026 Meander Travel Co. All Right Reserved</div>
    <div class="fsocial"><span></span><span></span></div>
    <div class="flinks"><span>Terms &amp;</span><span>|</span><span>Conditions</span><span>|</span><span>Privacy Policy</span></div>
  </footer>
</section>

<!-- Family Trips -->
<section class="page" style="left:223px;top:564px;height:677px">
  <header class="topbar">
    <div class="phone"><svg viewBox="0 0 10 10"><path d="M2 1l2 0 1 2.5-1.3 1a6 6 0 0 0 2.8 2.8l1-1.3L10 7v2a1 1 0 0 1-1 1A9 9 0 0 1 0 1a1 1 0 0 1 1-1z" fill="#b9842f"/></svg>111.111.1111</div>
    <div class="brand">Meander</div>
    <div class="social"><span></span><span></span></div>
  </header>
  <nav class="nav"><span>Home</span><span>Brimwell Vacations</span><span>Family Trips</span><span>Texas Road Trips</span><span>Other Destinations</span><span>About Us</span><span>Contact</span></nav>
  <div class="hero hero-beach" role="img" aria-label="Photo of a beach at sunset">
    <h1>Family Trips</h1>
    <p>Discover amazing family trips designed to create unforgettable memories. Choose your preferred trip and we'll handle the rest.</p>
    <svg class="tear" viewBox="0 0 474 16" preserveAspectRatio="none"><path d="M0 16V9l18 2 14-5 20 4 22-6 16 5 24-3 18 4 20-6 26 5 18-2 22 4 20-5 24 3 18-4 22 5 20-3 26 4 18-6 22 5 20-2 24 3 22-5 20 4V16z" fill="#fff"/></svg>
  </div>
  <div class="thumbs">
    <div class="thumb t-road" role="img" aria-label="Photo of a desert highway"></div>
    <div class="thumb t-peak" role="img" aria-label="Photo of a hiker on a mountain"></div>
    <div class="thumb t-shore" role="img" aria-label="Photo of a calm shoreline"></div>
    <div class="thumb t-street" role="img" aria-label="Photo of travelers with suitcases"></div>
    <div class="thumb t-selfie" role="img" aria-label="Photo of travelers taking a selfie"></div>
    <div class="thumb t-reef" role="img" aria-label="Photo of an underwater reef"></div>
  </div>
  <form class="card">
    <div class="card-title">Trip Inquiry Form</div>
    <div class="field">Which Trip Are You Interested In?<svg class="chev" viewBox="0 0 10 6"><path d="M1 1l4 4 4-4" fill="none" stroke="#777" stroke-width="1.5"/></svg></div>
    <div class="field">How Many People In Your Party?</div>
    <div class="label">Start Date</div>
    <div class="field">mm/dd/yyyy<span class="cal"></span></div>
    <div class="label">End Date</div>
    <div class="field">mm/dd/yyyy<span class="cal"></span></div>
    <div class="field">What Kind of Trip?<svg class="chev" viewBox="0 0 10 6"><path d="M1 1l4 4 4-4" fill="none" stroke="#777" stroke-width="1.5"/></svg></div>
    <div class="field area">Any additional notes</div>
    <div class="btn">Submit Trip Request</div>
  </form>
  <footer class="footer" style="height:76px">
    <svg class="ftear" viewBox="0 0 474 15" preserveAspectRatio="none"><path d="M0 15V8l22-3 18 4 24-5 20 3 22-4 18 5 26-2 20 3 22-6 18 4 24-2 20 4 22-5 18 3 26-4 20 5 22-3 18 2 24-6 22 1 18-4 16 3 20-3V15z" fill="#0b4a5a"/></svg>
    <div class="fbrand">Meander</div>
    <div class="finfo"><span><svg viewBox="0 0 10 10"><path d="M2 1l2 0 1 2.5-1.3 1a6 6 0 0 0 2.8 2.8l1-1.3L10 7v2a1 1 0 0 1-1 1A9 9 0 0 1 0 1a1 1 0 0 1 1-1z" fill="#fff"/></svg>111.111.1111</span><span><svg viewBox="0 0 10 10"><rect x="0" y="2" width="10" height="7" fill="#fff"/></svg>hello@meandertravel.example</span></div>
    <div class="fcopy">2026 Meander Travel Co. All Right Reserved</div>
    <div class="fsocial"><span></span><span></span></div>
    <div class="flinks"><span>Terms &amp;</span><span>|</span><span>Conditions</span><span>|</span><span>Privacy Policy</span></div>
  </footer>
</section>

<!-- Road Trips -->
<section class="page" style="left:223px;top:1270px;height:756px">
  <header class="topbar">
    <div class="phone"><svg viewBox="0 0 10 10"><path d="M2 1l2 0 1 2.5-1.3 1a6 6 0 0 0 2.8 2.8l1-1.3L10 7v2a1 1 0 0 1-1 1A9 9 0 0 1 0 1a1 1 0 0 1 1-1z" fill="#b9842f"/></svg>111.111.1111</div>
    <div class="brand">Meander</div>
    <div class="social"><span></span><span></span></div>
  </header>
  <nav class="nav"><span>Home</span><span>Brimwell Vacations</span><span>Family Trips</span><span>Texas Road Trips</span><span>Other Destinations</span><span>About Us</span><span>Contact</span></nav>
  <div class="hero hero-canyon" role="img" aria-label="Photo of a road winding through red rock canyon">
    <h1>Road Trips from Texas</h1>
    <svg class="tear" viewBox="0 0 474 16" preserveAspectRatio="none"><path d="M0 16V9l18 2 14-5 20 4 22-6 16 5 24-3 18 4 20-6 26 5 18-2 22 4 20-5 24 3 18-4 22 5 20-3 26 4 18-6 22 5 20-2 24 3 22-5 20 4V16z" fill="#fff"/></svg>
  </div>
  <div class="section-head">
    <h2>Explore Road Trip Options</h2>
    <p>In partnership with Piney Road Van Rentals (Tyler, TX), we make your road trips easy, comfortable and family-friendly.</p>
  </div>
  <table class="trips">
    <thead><tr><th>Trip Name</th><th>Destination</th><th>Duration</th><th>Estimated Cost</th><th>Best For</th></tr></thead>
    <tbody>
      <tr><td>Trip A</td><td>Hill Country, TX</td><td>3 Days</td><td>Budget</td><td>Families</td></tr>
      <tr class="alt"><td>Trip B</td><td>Galveston Beach</td><td>5 Days</td><td>Moderate</td><td>Family + Kids</td></tr>
      <tr><td>Trip C</td><td>Big Bend National Park</td><td>4 Days</td><td>Luxury</td><td>Adventure Lovers</td></tr>
    </tbody>
  </table>
  <form class="card">
    <div class="card-title">Road Trip Inquiry Form</div>
    <div class="field">Which Trip Are You Interested In?<svg class="chev" viewBox="0 0 10 6"><path d="M1 1l4 4 4-4" fill="none" stroke="#777" stroke-width="1.5"/></svg></div>
    <div class="field">How Many People In Your Party?</div>
    <div class="field">Do You Need a Van Rental?</div>
    <div class="label">Start Date</div>
    <div class="field">mm/dd/yyyy<span class="cal"></span></div>
    <div class="label">End Date</div>
    <div class="field">mm/dd/yyyy<span class="cal"></span></div>
    <div class="field">What Kind of Trip?<svg class="chev" viewBox="0 0 10 6"><path d="M1 1l4 4 4-4" fill="none" stroke="#777" stroke-width="1.5"/></svg></div>
    <div class="field area">Any additional notes</div>
    <div class="btn">Submit Trip Request</div>
  </form>
  <footer class="footer" style="height:72px">
    <svg class="ftear" viewBox="0 0 474 15" preserveAspectRatio="none"><path d="M0 15V8l22-3 18 4 24-5 20 3 22-4 18 5 26-2 20 3 22-6 18 4 24-2 20 4 22-5 18 3 26-4 20 5 22-3 18 2 24-6 22 1 18-4 16 3 20-3V15z" fill="#0b4a5a"/></svg>
    <div class="fbrand">Meander</div>
    <div class="finfo"><span><svg viewBox="0 0 10 10"><path d="M2 1l2 0 1 2.5-1.3 1a6 6 0 0 0 2.8 2.8l1-1.3L10 7v2a1 1 0 0 1-1 1A9 9 0 0 1 0 1a1 1 0 0 1 1-1z" fill="#fff"/></svg>111.111.1111</span><span><svg viewBox="0 0 10 10"><rect x="0" y="2" width="10" height="7" fill="#fff"/></svg>hello@meandertravel.example</span></div>
    <div class="fcopy">2026 Meander Travel Co. All Right Reserved</div>
    <div class="fsocial"><span></span><span></span></div>
    <div class="flinks"><span>Terms &amp;</span><span>|</span><span>Conditions</span><span>|</span><span>Privacy Policy</span></div>
  </footer>
</section>

<!-- About -->
<section class="page" style="left:716px;top:1270px;height:558px">
  <header class="topbar">
    <div class="phone"><svg viewBox="0 0 10 10"><path d="M2 1l2 0 1 2.5-1.3 1a6 6 0 0 0 2.8 2.8l1-1.3L10 7v2a1 1 0 0 1-1 1A9 9 0 0 1 0 1a1 1 0 0 1 1-1z" fill="#b9842f"/></svg>111.111.1111</div>
    <div class="brand">Meander</div>
    <div class="social"><span></span><span></span></div>
  </header>
  <nav class="nav"><span>Home</span><span>Brimwell Vacations</span><span>Family Trips</span><span>Texas Road Trips</span><span>Other Destinations</span><span>About Us</span><span>Contact</span></nav>
  <div class="hero hero-beach" role="img" aria-label="Photo of a beach at sunset">
    <h1>About Our Family</h1>
    <svg class="tear" viewBox="0 0 474 16" preserveAspectRatio="none"><path d="M0 16V9l18 2 14-5 20 4 22-6 16 5 24-3 18 4 20-6 26 5 18-2 22 4 20-5 24 3 18-4 22 5 20-3 26 4 18-6 22 5 20-2 24 3 22-5 20 4V16z" fill="#fff"/></svg>
  </div>
  <div class="thumbs">
    <div class="thumb t-road" role="img" aria-label="Photo of a desert highway"></div>
    <div class="thumb t-peak" role="img" aria-label="Photo of a hiker on a mountain"></div>
    <div class="thumb t-shore" role="img" aria-label="Photo of a calm shoreline"></div>
    <div class="thumb t-street" role="img" aria-label="Photo of travelers with suitcases"></div>
    <div class="thumb t-selfie" role="img" aria-label="Photo of travelers taking a selfie"></div>
    <div class="thumb t-reef" role="img" aria-label="Photo of an underwater reef"></div>
  </div>
  <div class="about">
    <div class="about-photo" role="img" aria-label="Photo of a group of friends looking out at a city skyline"></div>
    <div class="about-text">
      <h2>About Our Family</h2>
      <p>We are a family-focused travel planning service dedicated to creating unforgettable experiences for families who love to explore the world together.</p>
      <p>Our journey started with a simple idea — to make travel easier, more personal, and completely stress-free for families. We understand how important it is to spend quality time with loved ones, and we believe every trip should become a lasting memory.</p>
      <p>We specialize in planning Brimwell vacations, road trips, family getaways, and destination experiences tailored to your needs, budget, and comfort.</p>
      <p>As a local and family-oriented business, we treat every client like part of our own family. From the first conversation to the final day of your trip, we are here to guide you every step of the way.</p>
    </div>
  </div>
  <footer class="footer" style="height:74px">
    <svg class="ftear" viewBox="0 0 474 15" preserveAspectRatio="none"><path d="M0 15V8l22-3 18 4 24-5 20 3 22-4 18 5 26-2 20 3 22-6 18 4 24-2 20 4 22-5 18 3 26-4 20 5 22-3 18 2 24-6 22 1 18-4 16 3 20-3V15z" fill="#0b4a5a"/></svg>
    <div class="fbrand">Meander</div>
    <div class="finfo"><span><svg viewBox="0 0 10 10"><path d="M2 1l2 0 1 2.5-1.3 1a6 6 0 0 0 2.8 2.8l1-1.3L10 7v2a1 1 0 0 1-1 1A9 9 0 0 1 0 1a1 1 0 0 1 1-1z" fill="#fff"/></svg>111.111.1111</span><span><svg viewBox="0 0 10 10"><rect x="0" y="2" width="10" height="7" fill="#fff"/></svg>hello@meandertravel.example</span></div>
    <div class="fcopy">2026 Meander Travel Co. All Right Reserved</div>
    <div class="fsocial"><span></span><span></span></div>
    <div class="flinks"><span>Terms &amp;</span><span>|</span><span>Conditions</span><span>|</span><span>Privacy Policy</span></div>
  </footer>
</section>

<!-- Contact -->
<section class="page contact" style="left:716px;top:1847px;height:573px">
  <header class="topbar">
    <div class="phone"><svg viewBox="0 0 10 10"><path d="M2 1l2 0 1 2.5-1.3 1a6 6 0 0 0 2.8 2.8l1-1.3L10 7v2a1 1 0 0 1-1 1A9 9 0 0 1 0 1a1 1 0 0 1 1-1z" fill="#b9842f"/></svg>111.111.1111</div>
    <div class="brand">Meander</div>
    <div class="social"><span></span><span></span></div>
  </header>
  <nav class="nav"><span>Home</span><span>Brimwell Vacations</span><span>Family Trips</span><span>Texas Road Trips</span><span>Other Destinations</span><span>About Us</span><span>Contact</span></nav>
  <div class="hero hero-beach" role="img" aria-label="Photo of a beach at sunset">
    <h1>Contact Us</h1>
    <p>We'd love to hear from you. Let's plan your next unforgettable trip together.</p>
    <svg class="tear" viewBox="0 0 474 16" preserveAspectRatio="none"><path d="M0 16V9l18 2 14-5 20 4 22-6 16 5 24-3 18 4 20-6 26 5 18-2 22 4 20-5 24 3 18-4 22 5 20-3 26 4 18-6 22 5 20-2 24 3 22-5 20 4V16z" fill="#fff"/></svg>
  </div>
  <div class="chips">
    <div class="chip"><span class="dot"><svg viewBox="0 0 10 10"><path d="M2 1l2 0 1 2.5-1.3 1a6 6 0 0 0 2.8 2.8l1-1.3L10 7v2a1 1 0 0 1-1 1A9 9 0 0 1 0 1a1 1 0 0 1 1-1z" fill="#fff"/></svg></span><div><b>Phone</b><small>111.111.1111</small></div></div>
    <div class="chip"><span class="dot"><svg viewBox="0 0 10 10"><rect x="1" y="2.5" width="8" height="5.5" fill="#fff"/></svg></span><div><b>Email</b><small>hello@meandertravel.example</small></div></div>
  </div>
  <form class="card">
    <div class="card-title">Get in Touch</div>
    <div class="field">Name</div>
    <div class="field">Email</div>
    <div class="field">Phone</div>
    <div class="field area">Any details you want us to know?</div>
    <div class="btn">Submit Trip Request</div>
  </form>
  <footer class="footer" style="height:74px">
    <svg class="ftear" viewBox="0 0 474 15" preserveAspectRatio="none"><path d="M0 15V8l22-3 18 4 24-5 20 3 22-4 18 5 26-2 20 3 22-6 18 4 24-2 20 4 22-5 18 3 26-4 20 5 22-3 18 2 24-6 22 1 18-4 16 3 20-3V15z" fill="#0b4a5a"/></svg>
    <div class="fbrand">Meander</div>
    <div class="finfo"><span><svg viewBox="0 0 10 10"><path d="M2 1l2 0 1 2.5-1.3 1a6 6 0 0 0 2.8 2.8l1-1.3L10 7v2a1 1 0 0 1-1 1A9 9 0 0 1 0 1a1 1 0 0 1 1-1z" fill="#fff"/></svg>111.111.1111</span><span><svg viewBox="0 0 10 10"><rect x="0" y="2" width="10" height="7" fill="#fff"/></svg>hello@meandertravel.example</span></div>
    <div class="fcopy">2026 Meander Travel Co. All Right Reserved</div>
    <div class="fsocial"><span></span><span></span></div>
    <div class="flinks"><span>Terms &amp;</span><span>|</span><span>Conditions</span><span>|</span><span>Privacy Policy</span></div>
  </footer>
</section>

<div class="mark">Meander<br>Travel Co.</div>

</div>
</body>
</html>
```